MEDICAL CLINIC LETTERHEAD

Design is a letterhead for a non-profit medical center. The name of the clinic is VITARIDGE Community Health Center. Although the full name must be included, the community health center part is more of a description and should be less visible - i attached an example of what I mean by that (ATTACHED IMAGE IS AN EXAMPLE OF FONT SIZES NOT A DESIGN IDEA). Please design something modern, cool looking and unique because I can always download free templates.
Phone, email, website and etc will be added later.

Industry/Entity Type

MEDICAL

```html
<!DOCTYPE html>
<html lang="en">
<head>
<meta charset="utf-8">
<title>VITARIDGE Community Health Center – Letterhead</title>
<link href="https://fonts.googleapis.com/css2?family=Lato:wght@400;700&family=Arimo:wght@400&family=Allura&display=swap" rel="stylesheet">
<style>
  :root {
    --navy: #1a2b50;
    --gold: #a88e52;
    --ink: #2b2b2b;
    --muted: #3a3a3a;
    --paper: #ffffff;
    --backdrop: #e3e3e5;
  }
  * { box-sizing: border-box; margin: 0; padding: 0; }
  html, body {
    width: 1200px; height: 874px; overflow: hidden;
    background: var(--backdrop);
  }
  .letterhead {
    position: absolute; left: 306px; top: 22px;
    width: 588px; height: 830px;
    background: var(--paper);
    box-shadow: 0 2px 10px rgba(0,0,0,.12);
    overflow: hidden;
    font-family: "Lato", sans-serif;
    color: var(--ink);
  }
  .footer-swoosh { position: absolute; left: 0; top: 0; width: 588px; height: 830px; }

  .brand {
    position: absolute; left: 44px; top: 92px;
    display: flex; align-items: center; gap: 8px;
  }
  .brand-dot { width: 10px; height: 10px; border-radius: 50%; background: var(--gold); }
  .brand-name {
    font-family: "Lato", sans-serif; font-weight: 400;
    font-size: 26px; letter-spacing: 1px; color: var(--navy);
  }

  .contact {
    position: absolute; left: 372px; top: 44px;
    padding-left: 10px; border-left: 1px solid var(--gold);
    font-family: "Arimo", sans-serif; font-size: 8.5px; line-height: 1.3;
    color: #111;
  }
  .contact-name { margin-bottom: 3px; }
  .contact-list { list-style: none; }
  .contact-list li { display: flex; align-items: center; gap: 6px; margin-left: 6px; }
  .contact-list svg { width: 8px; height: 8px; fill: var(--gold); }

  .letter {
    position: absolute; left: 60px; top: 162px; width: 440px;
    font-size: 9px; line-height: 1.32; color: var(--muted);
  }
  .letter-date { margin-bottom: 10px; font-size: 9.5px; }
  .recipient { margin-bottom: 10px; font-size: 9.5px; }
  .recipient-block { margin-bottom: 10px; }
  .salutation { font-weight: 700; font-size: 11px; color: var(--ink); margin: 6px 0 8px; }
  .letter p.body { margin-bottom: 12px; }
  .closing { margin-top: 18px; font-size: 9.5px; }
  .signature {
    font-family: "Allura", cursive; font-size: 34px;
    color: var(--ink); margin: 2px 0 0 28px;
  }
</style>
</head>
<body>
  <main class="letterhead">
    <svg class="footer-swoosh" viewBox="0 0 588 830" aria-hidden="true">
      <path d="M588 690 C 520 735 430 775 300 806 C 430 782 530 745 588 702 Z" fill="var(--gold)"/>
      <path d="M0 830 C 230 818 470 770 588 708 L588 830 Z" fill="var(--navy)"/>
    </svg>

    <div class="brand">
      <span class="brand-dot"></span>
      <span class="brand-name">VITARIDGE</span>
    </div>

    <address class="contact">
      <div class="contact-name">VITARIDGE Community<br>Health Center</div>
      <ul class="contact-list">
        <li><svg viewBox="0 0 10 10"><path d="M2 1 L4 1 L4.6 3.2 L3.5 4 Q4.5 6 6 6.5 L6.8 5.4 L9 6 L9 8 Q5 9.5 1 3 Z"/></svg>555-214-0376</li>
        <li><svg viewBox="0 0 10 10"><path d="M0 2 H10 V8 H0 Z M0.8 2.6 L5 5.6 L9.2 2.6 V2.6 L5 5 Z" fill-rule="evenodd"/></svg>hello@vitaridge-mail.org</li>
        <li><svg viewBox="0 0 10 10"><circle cx="5" cy="5" r="4.5"/></svg>www.vitaridge-web.org</li>
      </ul>
    </address>

    <article class="letter">
      <p class="letter-date">Feb-03-2022</p>
      <p class="recipient">Mr. Daniel Reyes<br>President</p>
      <p class="recipient recipient-block">Northfield Partners<br>48 Maple Avenue, Suite# 10<br>City, State, 120023</p>
      <p class="salutation">Dear Mr, Daniel</p>
      <p class="body">Lorem ipsum dolor sit amet, consectetur adipisicing elit, sed do eiusmod tempor incididunt ut labore et dolore magna aliqua. Ut enim ad minim veniam, quis nostrud exercitation ullamco laboris nisi ut aliquip ex ea commodo consequat. Duis aute irure dolor in reprehenderit in voluptate velit esse cillum dolore eu fugiat nulla pariatur.</p>
      <p class="body">Lorem ipsum dolor sit amet, consectetur adipisicing elit, sed do eiusmod tempor incididunt ut labore et dolore magna aliqua. Ut enim ad minim veniam, quis nostrud exercitation ullamco laboris nisi ut aliquip ex ea commodo consequat. Duis aute irure dolor in reprehenderit in voluptate velit esse cillum dolore eu fugiat nulla pariatur.</p>
      <p class="body">Lorem ipsum dolor sit amet, consectetur adipisicing elit, sed do eiusmod tempor incididunt ut labore et dolore magna aliqua. Ut enim ad minim veniam, quis nostrud exercitation ullamco laboris nisi ut aliquip ex ea commodo consequat.</p>
      <p class="body">Excepteur sint occaecat cupidatat non proident, sunt in culpa qui officia deserunt mollit anim id est laborum. re et dolore magnam aliquam quaerat voluptatem.</p>
      <p class="closing">Regards</p>
      <p class="signature">Laura Bennett</p>
    </article>
  </main>
</body>
</html>
```